SkyvornQ Business Cards and Stationary Design

Need a design for our business cards and stationary. I want to carry on the theme of the logo. I want the business cards to have a design on the back. I would like the business cards and the stationary to carry the same theme, design scheme, and branding

Target Market(s)

Airlines and Maintenance Facilities

Industry/Entity Type

Aviation

Contact Information for Business Card

Name
Position Title
Address: 4827 Trellis Hollow Road, Larkmere, Calden, 34951
Office Number
Mobile Number
Email
Website

Font styles to use
Serif
Sans Serif

Colors

Designer to choose colors to be used in the design.

```html
<!DOCTYPE html>
<html lang="en">
<head>
<meta charset="utf-8">
<title>SkyvornQ Business Card</title>
<link rel="stylesheet" href="https://fonts.googleapis.com/css2?family=Open+Sans:wght@400;600;700;800&display=swap">
<style>
  :root {
    --navy: #0d3370;
    --sky: #1e7fd0;
    --paper: #f4f5f7;
    --tab-grey: #a9abb0;
    --backdrop: #2c2c2e;
    --ink-light: #ffffff;
    --ink-muted: #555a63;
  }
  * { box-sizing: border-box; margin: 0; padding: 0; }
  html, body { width: 1200px; height: 900px; overflow: hidden; }
  body {
    background: var(--backdrop);
    font-family: "Open Sans", Arial, sans-serif;
    position: relative;
  }
  .card {
    position: absolute;
    left: 290px;
    width: 620px;
    height: 354px;
    border-radius: 18px;
    overflow: hidden;
    background: var(--paper);
    box-shadow: 0 10px 28px rgba(0,0,0,.45);
  }
  .card--front { top: 64px; }
  .card--back { top: 482px; }

  /* front */
  .brand-side {
    position: absolute; left: 0; top: 0; width: 300px; height: 100%;
    display: flex; align-items: center; justify-content: center; gap: 12px;
  }
  .brand-mark {
    width: 26px; height: 26px; border-radius: 50%;
    border: 4px solid var(--sky);
    flex: none;
  }
  .brand-name {
    font-weight: 800; font-size: 38px; letter-spacing: 1px; color: var(--navy);
  }
  .contact-side {
    position: absolute; left: 300px; top: 0; right: 0; height: 100%;
    background: var(--navy); color: var(--ink-light);
    padding: 64px 24px 0 58px;
  }
  .contact-tab {
    position: absolute; left: 292px; top: 62px; width: 22px; height: 122px;
    background: var(--tab-grey);
  }
  .person-name { font-weight: 700; font-size: 17px; letter-spacing: .3px; }
  .person-role { font-size: 14px; margin-bottom: 14px; }
  .contact-list { list-style: none; font-size: 14px; line-height: 1.55; padding-left: 20px; }
  .contact-list li { display: flex; align-items: center; gap: 8px; }
  .contact-list svg { width: 12px; height: 12px; fill: var(--ink-light); flex: none; }
  .address { font-size: 14px; line-height: 1.45; margin-top: 12px; padding-left: 20px; }

  /* back */
  .band {
    position: absolute; top: 0; height: 100%; width: 62px; background: var(--navy);
  }
  .band--left { left: 50px; }
  .band--right { right: 50px; }
  .back-brand {
    position: absolute; left: 0; right: 0; top: 122px;
    display: flex; align-items: center; justify-content: center; gap: 16px;
  }
  .back-brand .brand-mark { width: 40px; height: 40px; border-width: 6px; }
  .back-brand .brand-name { font-size: 48px; }
  .website {
    position: absolute; right: 132px; bottom: 44px;
    font-size: 17px; letter-spacing: 3px; color: var(--ink-muted);
  }
</style>
</head>
<body>
  <section class="card card--front">
    <div class="brand-side">
      <span class="brand-mark"></span>
      <span class="brand-name">SkyvornQ</span>
    </div>
    <div class="contact-side">
      <p class="person-name">DARA WHITLOW</p>
      <p class="person-role">President</p>
      <ul class="contact-list">
        <li><svg viewBox="0 0 12 12"><path d="M2.5 1l2 2.3-1 1.2a7 7 0 0 0 4 4l1.2-1 2.3 2-1.3 1.5C5.5 11 1 6.5 1 2.3z"/></svg>001 555 0148</li>
        <li><svg viewBox="0 0 12 12"><path d="M3.5 0h5a1 1 0 0 1 1 1v10a1 1 0 0 1-1 1h-5a1 1 0 0 1-1-1V1a1 1 0 0 1 1-1zM4 1.5v7.5h4V1.5z"/></svg>001 555 0149</li>
        <li><svg viewBox="0 0 12 12"><path d="M0 2h12v8H0zM1 3l5 3.5L11 3v-.2H1z" fill-rule="evenodd"/></svg>info@skyvornq.com</li>
      </ul>
      <p class="address">4827 Trellis Hollow Road,<br>Larkmere, Calden, 34951</p>
    </div>
    <div class="contact-tab"></div>
  </section>

  <section class="card card--back">
    <div class="band band--left"></div>
    <div class="band band--right"></div>
    <div class="back-brand">
      <span class="brand-mark"></span>
      <span class="brand-name">SkyvornQ</span>
    </div>
    <p class="website">www.skyvornq.com</p>
  </section>
</body>
</html>
```